Website for Torvel Capital - investment banking firm

We have a corporate identity (thanks to Ravinka/31842) and want to extend that into a website design.  See the attached zipped files.
We have software folks in-house to do the coding.
See the attached Project Brief & Notes for more details.  Don't worry about the actual text - lorem ipsum will be fine.
The server will be Apache.
Thank you!
Desmond

Industry/Entity Type
Investment

```html
<!DOCTYPE html>
<html lang="en">
<head>
<meta charset="utf-8">
<title>Torvel Capital</title>
<link href="https://fonts.googleapis.com/css2?family=Cormorant+Garamond:wght@500;600&family=Lora:wght@400&family=Figtree:wght@400;600;700&display=swap" rel="stylesheet">
<style>
:root{
  --brand:#0b56a9;
  --brand-dark:#003c7e;
  --nav-link:#8dbbef;
  --ink:#5b6470;
  --muted:#8a929c;
  --footer-bg:#dfe5ee;
  --heading:#0b4f9e;
  --white:#ffffff;
}
*{margin:0;padding:0;box-sizing:border-box}
html,body{width:1145px;height:1200px;overflow:hidden;background:var(--white)}
body{font-family:"Figtree",sans-serif;color:var(--ink)}
.page{position:relative;width:1280px;height:1341px;transform:scale(0.8945);transform-origin:0 0;overflow:hidden}
.abs{position:absolute}

.site-header{left:0;top:0;width:1280px;height:87px;background:repeating-linear-gradient(135deg,#fff 0 3px,#f5f7fa 3px 4px)}
.brand{left:172px;top:18px;display:flex;align-items:center;gap:14px}
.brand-mark{width:40px;height:40px;background:var(--brand)}
.brand-name{font-family:"Cormorant Garamond",serif;font-weight:600;font-size:36px;color:var(--brand);letter-spacing:.5px}

.main-nav{left:0;top:87px;width:1280px;height:58px;background:var(--brand);display:flex;align-items:center;padding-left:192px}
.main-nav a{font-weight:700;font-size:15.5px;color:var(--nav-link);text-decoration:none;margin-right:38px;letter-spacing:.2px}
.main-nav a.active{color:var(--white)}

.hero{left:0;top:145px;width:1280px;height:511px;background:linear-gradient(160deg,#1e5f8e 0%,#7fb6d9 35%,#d7e8f2 55%,#6d9ec0 75%,#2a5578 100%)}
.slider-arrow{top:182px;width:55px;height:60px;background:rgba(10,40,70,.45);display:flex;align-items:center;justify-content:center}
.slider-arrow.prev{left:0}
.slider-arrow.next{right:0;background:transparent}
.hero-card{left:630px;top:105px;width:490px;min-height:224px;background:rgba(255,255,255,.9);padding:36px 22px 38px}
.hero-card h1{font-family:"Cormorant Garamond",serif;font-weight:600;font-variant:small-caps;font-size:41px;line-height:44px;color:var(--heading);white-space:nowrap;letter-spacing:-.2px}
.hero-card p{margin-top:14px;width:385px;font-size:16.5px;line-height:24px;color:#5a5f66;padding-left:3px}

.feature{top:656px;width:320px;height:299px;padding:32px 33px;color:var(--white)}
.feature h2{font-family:"Lora",serif;font-weight:400;font-size:23px;margin-bottom:26px}
.feature p{font-size:12.5px;line-height:18px}
.f-about{left:160px;background:linear-gradient(180deg,#0c4d98,#023f80)}
.f-services{left:480px;background:linear-gradient(180deg,#0a66c9,#0a4f9e);padding-left:29px;padding-right:6px}
.f-clients{left:800px;background:linear-gradient(180deg,#4a95dd,#2f67a2);padding-left:30px}
.services-title{font-weight:700;font-size:12.5px;margin-bottom:8px}
.services-list{list-style:none;font-size:12.5px;white-space:nowrap;letter-spacing:-.1px}
.services-list li{margin-bottom:7px;display:flex;align-items:center;gap:6px}
.services-list li::before{content:"";border-left:5px solid var(--white);border-top:4px solid transparent;border-bottom:4px solid transparent}
.read-more{position:absolute;left:42px;top:234px;width:79px;height:33px;border-radius:17px;background:linear-gradient(#fff,#e9ebee);border:1px solid #c9ced4;color:#7b828b;font-size:11px;display:flex;align-items:center;justify-content:center}

.site-footer{left:0;top:1051px;width:1280px;height:244px;background:var(--footer-bg)}
.footer-brand{left:160px;top:37px;display:flex;align-items:center;gap:10px}
.footer-brand .brand-mark{width:30px;height:30px}
.footer-brand .brand-name{font-size:25px}
.footer-about{left:165px;top:92px;width:215px;font-size:13px;line-height:20px}
.footer-about p+p{margin-top:20px}
.footer-title{top:39px;font-weight:700;font-size:12.5px;letter-spacing:.6px;color:#5b6470}
.post{left:416px;display:flex;gap:14px}
.post-thumb{width:55px;height:54px;background:linear-gradient(135deg,#8a95a0,#3e4650)}
.post-text{font-size:13px;line-height:20px;width:150px}
.post-date{font-style:italic;font-size:11px;color:var(--muted)}
.newsletter-text{left:670px;top:70px;width:230px;font-size:13px;line-height:22px}
.subscribe{left:670px;top:131px;width:251px;height:37px;display:flex}
.subscribe .field{flex:1;background:#a9b4c5;color:var(--white);font-size:13px;padding:11px 14px}
.subscribe .btn{width:88px;background:#2e4f7a;color:var(--white);font-size:14px;display:flex;align-items:center;justify-content:center}
.contact-row{left:943px;display:flex;gap:14px;font-size:13px;line-height:20px}
.contact-row svg{flex:none;margin-top:2px}

.bottom-bar{left:0;top:1295px;width:1280px;height:46px;background:var(--brand);color:#cfe0f4;font-size:12.5px}
.bottom-bar .copy{position:absolute;left:165px;top:15px}
.bottom-bar .links{position:absolute;right:138px;top:15px;display:flex;gap:43px}
</style>
</head>
<body>
<div class="page">
  <header class="site-header abs">
    <div class="brand abs"><span class="brand-mark"></span><span class="brand-name">Torvel Capital</span></div>
  </header>

  <nav class="main-nav abs">
    <a class="active">HOME</a><a>HISTORY</a><a>CLIENTS</a><a>OUR TEAM</a><a>COMPLETED DEALS</a><a>CURRENT SEARCHES</a><a>CONTACT US</a>
  </nav>

  <section class="hero abs" role="img" aria-label="Photo looking up at glass office towers and a curved skybridge">
    <div class="slider-arrow prev abs"><svg width="12" height="18" viewBox="0 0 12 18"><path d="M10 2 3 9l7 7" fill="none" stroke="#fff" stroke-width="2.5"/></svg></div>
    <div class="slider-arrow next abs"><svg width="12" height="18" viewBox="0 0 12 18"><path d="M2 2l7 7-7 7" fill="none" stroke="#fff" stroke-width="2.5"/></svg></div>
    <div class="hero-card abs">
      <h1>Global, Professional,<br>Trusted.</h1>
      <p>Torvel Capital is an independent investment bank working for buyers in a number of industries.</p>
    </div>
  </section>

  <article class="feature f-about abs">
    <h2>Who We Are</h2>
    <p>Torvel Capital is an independent investment bank working for buyers in a number of industries. We utilize exceptional technology in finding companies to meet our client's search criteria. We will not waste a buyer's time, a seller's time, or our own time.</p>
    <span class="read-more">Read More</span>
  </article>
  <article class="feature f-services abs">
    <h2>Our Services</h2>
    <div class="services-title">OUR SERVICES INCLUDE::</div>
    <ul class="services-list">
      <li>Buy-Side Acquisitions</li>
      <li>Recapitalizations &amp; Growth Capital Partnerships</li>
      <li>Sell-Side Transactions</li>
    </ul>
    <span class="read-more">Read More</span>
  </article>
  <article class="feature f-clients abs">
    <h2>Our Clients</h2>
    <p>Torvel Capital has a diverse array of clients ranging from multi-billion dollar strategic acquirers to large private equity funds. We will not engage a client as a buyer if we believe there is any chance of them wasting our time or a prospective seller's time.</p>
    <span class="read-more">Read More</span>
  </article>

  <footer class="site-footer abs">
    <div class="footer-brand abs"><span class="brand-mark"></span><span class="brand-name">Torvel Capital</span></div>
    <div class="footer-about abs">
      <p>Donec volutpat, mi vel egestas eleifend, dolor arcu iaculis nunc. Fusce gravida tortor felis, ac dictum risus</p>
      <p>sagittis id. Morbi posuere justo eleifend libero ultricies ultrices.</p>
    </div>

    <div class="footer-title abs" style="left:416px">RECENT POST</div>
    <div class="post abs" style="top:76px">
      <div class="post-thumb" role="img" aria-label="Photo of two business people in conversation"></div>
      <div class="post-text">Fusce gravida tortor felis, ac dictum risus sagittis<div class="post-date">October 15, 2013</div></div>
    </div>
    <div class="post abs" style="top:154px">
      <div class="post-thumb" role="img" aria-label="Photo of hands using a tablet" style="background:linear-gradient(135deg,#c7d3de,#5d6b7a)"></div>
      <div class="post-text">Fusce gravida tortor felis, ac dictum risus sagittis<div class="post-date">October 15, 2013</div></div>
    </div>

    <div class="footer-title abs" style="left:671px;top:38px">NEWSLETTER</div>
    <p class="newsletter-text abs">Ipsum dolor sit amet, teft consecte tur adipiscing elit ut eunt.</p>
    <div class="subscribe abs"><span class="field">Email Address</span><span class="btn">Subscribe</span></div>

    <div class="footer-title abs" style="left:943px">CONTACT DETAILS</div>
    <div class="contact-row abs" style="top:73px">
      <svg width="18" height="16" viewBox="0 0 18 16"><path d="M3 1l3 0 1.5 4-2 1.5c1 2 2.5 3.5 4.5 4.5L11.5 9l4 1.5 0 3c-7 1-13-5-12.5-12.5z" fill="#8a929c"/></svg>
      <span>+1800-123-4567</span>
    </div>
    <div class="contact-row abs" style="top:103px">
      <svg width="18" height="16" viewBox="0 0 18 16"><rect x="2" y="3" width="14" height="10" fill="none" stroke="#8a929c" stroke-width="1.5"/><path d="M2 3l7 6 7-6" fill="none" stroke="#8a929c" stroke-width="1.5"/></svg>
      <span>info@yourwebsite.com</span>
    </div>
    <div class="contact-row abs" style="top:133px">
      <svg width="18" height="20" viewBox="0 0 18 20"><path d="M9 1a6 6 0 0 0-6 6c0 4.5 6 12 6 12s6-7.5 6-12a6 6 0 0 0-6-6z" fill="#8a929c"/><circle cx="9" cy="7" r="2.2" fill="#dfe5ee"/></svg>
      <span>Your Address, Your Country<br>Your Zip Code</span>
    </div>
  </footer>

  <div class="bottom-bar abs">
    <span class="copy">Copyright © 2014 - TorvelCapital. All Rights reserved</span>
    <span class="links"><span>Privacy Policy</span><span>Sitemap</span></span>
  </div>
</div>
</body>
</html>
```